Create modern and sleek business card for luxury real estate company

We're a "boutique" real estate office looking for a design that gets across a highly modern luxury brand. Blacks and whites are probably the best colors unless we try a silver foil for the logo. I've attached a version of our current logo here. I'd like to swap out the current font on there with Gotham Light Regular.

I'm looking to have one side of the card have the logo with the space for our agents info on the other side.

Target Market(s)

Young professionals in a "luxury" headspace

Industry/Entity Type

Real estate

Contact Information for Business Card

A place for agent name, cell number, website. The slogan "Thoughtfully Modern Home Living".

Font styles to use
Other font styles liked:
• Gotham Regular

Colors

Designer to choose only greyscale colors for use in the design.

Requirements
Must have
• Matte black as the background color. Clean lines and use of contrast. A specific design aspect that will use silver foil.
Nice to have
• Up in the air on integrating a QR code
Should not have
• Any houses or other real estate related design (ex: a clip art house)

```html
<!DOCTYPE html>
<html lang="en">
<head>
<meta charset="utf-8">
<title>Marlow Realty – Business Card</title>
<link href="https://fonts.googleapis.com/css2?family=Montserrat:wght@300;400;500&display=swap" rel="stylesheet">
<style>
  :root {
    --backdrop: #a9aaa5;
    --card: #2f2f30;
    --ink: #f2f2f2;
    --ink-soft: #cfcfcf;
    --rule: #bdbdbd;
  }
  * { margin: 0; padding: 0; box-sizing: border-box; }
  html, body {
    width: 1200px; height: 801px; overflow: hidden;
    background: var(--backdrop);
    font-family: "Montserrat", sans-serif;
    color: var(--ink);
  }
  .card {
    position: absolute;
    width: 540px; height: 309px;
    background: var(--card);
    border-radius: 18px;
    box-shadow: 0 14px 30px rgba(0,0,0,.28);
  }
  .card--agent { left: 40px; top: 100px; }
  .card--brand { left: 620px; top: 392px; }

  /* Brand lockup */
  .brand { display: flex; align-items: center; }
  .brand__mark {
    border: 2px solid var(--ink);
    border-radius: 50%;
    flex-shrink: 0;
  }
  .brand__name {
    font-weight: 400;
    text-transform: uppercase;
    line-height: 1.08;
    letter-spacing: .04em;
    color: var(--ink);
  }

  /* Agent side */
  .card--agent .brand { position: absolute; left: 34px; top: 34px; }
  .card--agent .brand__mark { width: 44px; height: 44px; margin-right: 12px; }
  .card--agent .brand__name { font-size: 17px; }

  .agent-rule {
    position: absolute; left: 34px; right: 34px; top: 196px;
    height: 1px; background: var(--rule);
  }
  .agent-name {
    position: absolute; right: 34px; top: 166px;
    font-size: 19px; font-weight: 500; letter-spacing: .03em;
    text-transform: uppercase;
  }
  .agent-title {
    position: absolute; right: 34px; top: 203px;
    font-size: 12px; font-weight: 300; color: var(--ink-soft);
  }
  .contacts {
    position: absolute; left: 34px; top: 214px;
    list-style: none; font-size: 13px; font-weight: 300; line-height: 1.55;
  }
  .contacts li { display: flex; align-items: center; gap: 8px; }
  .contacts svg { width: 10px; height: 10px; stroke: var(--ink); fill: none; stroke-width: 1.4; }

  /* Brand side */
  .card--brand .brand { position: absolute; left: 90px; top: 72px; }
  .card--brand .brand__mark { width: 100px; height: 100px; margin-right: 22px; }
  .card--brand .brand__name { font-size: 38px; }
  .slogan {
    position: absolute; left: 0; right: 0; bottom: 46px;
    text-align: center; font-size: 15px; font-weight: 300; letter-spacing: .1em;
    text-transform: uppercase; color: var(--ink);
  }
</style>
</head>
<body>

<section class="card card--agent">
  <div class="brand">
    <span class="brand__mark"></span>
    <span class="brand__name">Marlow<br>Realty</span>
  </div>
  <div class="agent-name">Daniel Hart</div>
  <div class="agent-rule"></div>
  <div class="agent-title">Director</div>
  <ul class="contacts">
    <li><svg viewBox="0 0 10 10"><path d="M2 1l2 2-1 1.5 2.5 2.5L7 6l2 2-1.5 1.5C5 9.5.5 5 .5 2.5z"/></svg>555.204.7788</li>
    <li><svg viewBox="0 0 10 10"><rect x=".7" y="2" width="8.6" height="6"/><path d="M.7 2L5 5.5 9.3 2"/></svg>hello@marlowrealty.com</li>
    <li><svg viewBox="0 0 10 10"><circle cx="5" cy="5" r="4.2"/><path d="M.8 5h8.4M5 .8c-2 2.5-2 5.9 0 8.4M5 .8c2 2.5 2 5.9 0 8.4"/></svg>www.marlowrealty.com</li>
  </ul>
</section>

<section class="card card--brand">
  <div class="brand">
    <span class="brand__mark"></span>
    <span class="brand__name">Marlow<br>Realty</span>
  </div>
  <p class="slogan">Thoughtfully Modern Home Living</p>
</section>

</body>
</html>
```